A website for a Maltese Law Firm

Our law firm needs a website to further its business. The site should have a simple yet effective design. We would need the following sections: About us, Practice Areas, About Malta, Contact. These should be further split as follows:

About us: Our firm, Our values, What others say, Offices

Practice Areas: Crimimal, Citizenship & Residence, Sovereign Patron Pathway, Criminal Defence, Civil Litigation, Arbitration and ADR, Commercial and Corporate, Media Law.

About Malta: just one section.

Contact: Just one section

We would also need a news feed at the front of the site to include latest news regarding our cases.

At the bottom we need a section for our Terms and a Privacy Statement.

Our logo is being attached.

Target Market(s)

All clients looking for legal assistance in Malta

Industry/Entity Type

Legal

Coding

Coded - Design and coding required

Number of Pages Required

1 page

Requirements
Must have
• It must be simple yet striking.

```html
<!DOCTYPE html>
<html lang="en">
<head>
<meta charset="utf-8">
<title>Mercieca &amp; Ellul Advocates</title>
<link rel="stylesheet" href="https://fonts.googleapis.com/css2?family=Cinzel:wght@400;600&family=Open+Sans:ital,wght@0,400;0,600;0,700;1,400&display=swap">
<style>
:root{
  --blue:#0b6bb0;
  --blue-dark:#0a5a95;
  --ink:#1d1d1d;
  --text:#5c5c5c;
  --muted:#8a8a8a;
  --line:#e3e3e3;
  --pale:#e9ecef;
  --footer:#222428;
  --footer-text:#c8c8c8;
  --white:#ffffff;
}
*{box-sizing:border-box;margin:0;padding:0}
html,body{width:1200px;height:2557px;overflow:hidden}
body{font-family:"Open Sans",Arial,sans-serif;color:var(--text);background:var(--white);position:relative}
.abs{position:absolute}
.serif{font-family:"Cinzel",Georgia,serif}

/* header */
.site-header{position:absolute;left:0;top:0;width:1200px;height:85px;background:var(--white);border-top:5px solid var(--blue)}
.brand{position:absolute;left:99px;top:20px;width:280px;text-align:center;font-family:"Cinzel",Georgia,serif;font-weight:600;color:var(--ink);line-height:1}
.brand .name{font-size:30px;letter-spacing:.5px;display:block}
.brand .sub{font-size:11px;letter-spacing:4px;display:block;margin-top:4px}
.main-nav a{position:absolute;top:38px;font-family:"Cinzel",Georgia,serif;font-size:15px;color:var(--ink);text-decoration:none;font-weight:600}
.main-nav a.active{color:var(--blue)}

/* hero */
.hero{position:absolute;left:0;top:85px;width:1200px;height:421px;background:linear-gradient(135deg,#3a4a5c 0%,#1e3346 45%,#26394b 65%,#6a5a45 100%)}
.hero h1{position:absolute;left:99px;top:115px;font-family:"Cinzel",Georgia,serif;font-weight:400;font-size:50px;color:var(--white);letter-spacing:1px}
.hero p{position:absolute;left:99px;top:180px;width:600px;font-size:18px;line-height:27px;color:var(--white);font-weight:600}
.btn-outline{position:absolute;left:99px;top:254px;width:148px;height:42px;background:var(--blue);border:2px solid var(--white);color:var(--white);font-size:14px;font-weight:700;display:flex;align-items:center;justify-content:center}
.hero .dots{position:absolute;left:537px;top:365px;display:flex;gap:6px}
.hero .dots span{width:28px;height:5px;background:var(--white);border-radius:3px}
.hero .dots span.on{background:var(--blue)}

/* welcome */
.section-title{position:absolute;left:0;width:1200px;text-align:center;font-family:"Cinzel",Georgia,serif;color:var(--ink);font-size:30px;font-weight:600}
.intro{position:absolute;left:170px;top:600px;width:860px;text-align:center;font-size:12.5px;line-height:26px;color:var(--text)}
.feature{position:absolute;top:674px;width:320px;text-align:center}
.feature .badge{width:112px;height:112px;margin:0 auto;border-radius:50%;border:3px solid var(--blue);padding:4px}
.feature .badge div{width:100%;height:100%;border-radius:50%;background:var(--blue);display:flex;align-items:center;justify-content:center}
.feature h3{font-family:"Cinzel",Georgia,serif;font-size:20px;color:var(--ink);font-weight:600;margin-top:22px;letter-spacing:1px}
.feature p{font-size:12.5px;line-height:22px;margin-top:10px;color:var(--text)}
.read-more{font-size:13px;font-weight:700;color:var(--blue);display:block;margin-top:12px}

/* practice areas */
.practice{position:absolute;left:0;top:980px;width:1200px;height:420px;background:var(--pale)}
.practice-panel{position:absolute;left:102px;top:125px;width:996px;height:242px;background:var(--white);border:1px solid #d9dde1}
.area-list{position:absolute;top:0;width:264px;height:100%}
.area-list li{list-style:none;height:56px;margin:0 14px 0 0;border-bottom:1px solid var(--line);font-size:12.5px;color:var(--text);display:flex;align-items:center;padding-left:30px}
.area-list li.active{background:var(--blue);color:var(--white);margin-right:0;border-bottom:none}
.area-list.right li{margin:0 0 0 0;padding-left:26px}
.area-feature{position:absolute;left:264px;top:0;width:468px;height:100%;background:linear-gradient(180deg,#4e3e35 0%,#2f2622 55%,#5a4434 100%)}
.area-feature h4{position:absolute;top:112px;width:100%;text-align:center;font-family:"Cinzel",Georgia,serif;font-size:20px;color:var(--white);font-weight:600}
.area-feature p{position:absolute;top:150px;left:30px;width:408px;text-align:center;font-size:12.5px;line-height:26px;color:var(--white)}

/* testimonials */
.testimonials{position:absolute;left:0;top:1400px;width:1200px;height:250px;background:var(--blue)}
.testimonials h2{position:absolute;top:34px;width:100%;text-align:center;font-family:"Cinzel",Georgia,serif;font-weight:600;font-size:29px;color:var(--white)}
.testimonials blockquote{position:absolute;left:230px;top:90px;width:740px;text-align:center;font-style:italic;font-size:14px;line-height:24.5px;color:var(--white)}
.testimonials cite{position:absolute;top:180px;width:100%;text-align:center;font-size:14px;color:var(--white);font-style:normal}
.testimonials cite em{font-style:italic}
.arrow{position:absolute;top:100px}

/* news */
.news-card{position:absolute;top:1749px;width:311px}
.news-card .photo{position:relative;width:311px;height:200px;border:4px solid #eee}
.news-card .date{position:absolute;right:0;bottom:10px;background:rgba(30,30,30,.85);color:var(--white);font-size:13px;padding:6px 10px}
.news-card h3{font-size:15px;font-weight:700;color:#333;line-height:23px;margin-top:12px}
.news-card p{font-size:12px;line-height:21px;color:var(--text);margin-top:8px}
.news-dots{position:absolute;left:581px;top:2134px;display:flex;gap:4px}
.news-dots span{width:11px;height:11px;border-radius:50%;background:#bbb}
.news-dots span.on{background:var(--blue)}

/* footer */
.site-footer{position:absolute;left:0;top:2199px;width:1200px;height:358px;background:var(--footer);border-top:6px solid var(--blue);color:var(--footer-text)}
.site-footer h5{position:absolute;top:32px;font-size:17px;color:var(--white);font-weight:700}
.footer-links{position:absolute;left:427px;top:66px;list-style:none;font-size:12.5px;line-height:25px;color:var(--footer-text)}
.footer-brand{position:absolute;left:99px;top:100px;width:280px;text-align:center;font-family:"Cinzel",Georgia,serif;font-weight:600;color:var(--white);line-height:1}
.footer-brand .name{font-size:28px;display:block}
.footer-brand .sub{font-size:10px;letter-spacing:4px;display:block;margin-top:4px}
.newsletter-text{position:absolute;left:595px;top:64px;width:260px;font-size:12.5px;line-height:19px;color:var(--footer-text)}
.email-field{position:absolute;left:595px;top:106px;width:254px;height:36px;background:var(--white);font-size:11px;color:#aaa;padding:11px 12px}
.btn-subscribe{position:absolute;left:595px;top:156px;width:87px;height:31px;background:var(--blue);color:var(--white);font-size:11px;font-weight:600;display:flex;align-items:center;justify-content:center}
.contact-list{position:absolute;left:910px;top:64px;list-style:none;font-size:12.5px;color:var(--footer-text)}
.contact-list li{display:flex;align-items:flex-start;gap:14px;line-height:25px}
.contact-list svg{margin-top:6px;flex:none}
.legal{position:absolute;left:99px;top:238px;width:700px;font-size:12.5px;color:var(--footer-text);line-height:19px}
.legal strong{color:var(--white);font-weight:600;display:block;margin-top:8px}
.social{position:absolute;left:1030px;top:277px;display:flex;gap:12px}
.social span{width:16px;height:16px;border-radius:50%;background:#d7d7d7}
</style>
</head>
<body>

<header class="site-header">
  <div class="brand"><span class="name">Mercieca &amp; Ellul</span><span class="sub">ADVOCATES</span></div>
  <nav class="main-nav">
    <a class="active" style="left:506px">HOME</a>
    <a style="left:578px">ABOUT US</a>
    <a style="left:680px">PRACTICE AREAS</a>
    <a style="left:830px">ABOUT MALTA</a>
    <a style="left:965px">CONTACT US</a>
    <svg class="abs" style="left:1090px;top:40px" width="14" height="14" viewBox="0 0 14 14"><circle cx="5.5" cy="5.5" r="4" fill="none" stroke="#1d1d1d" stroke-width="2"/><line x1="8.5" y1="8.5" x2="13" y2="13" stroke="#1d1d1d" stroke-width="2.4"/></svg>
  </nav>
</header>

<section class="hero" role="img" aria-label="Evening view of a Maltese harbour bay with boats and light trails along the waterfront road">
  <h1>MERCIECA &amp; ELLUL</h1>
  <p>At vero eos et accusamus et iusto odio dignissimos ducimus qui blanditiis praesenti um voluptatum deleniti atque corrupti quos dolores</p>
  <div class="btn-outline">READ MORE &gt;&gt;</div>
  <div class="dots"><span class="on"></span><span></span><span></span><span></span></div>
</section>

<section class="welcome">
  <h2 class="section-title" style="top:550px">Welcome to Mercieca &amp; Ellul</h2>
  <p class="intro">Nam libero tempore, cum soluta nobis est eligendi optio cumque nihil impedit quo minus id quod maxime placeat facere possimus, omnis voluptas assu menda est, omnis dolor repellenis aut rerum necessitatibus saepe eveniet ut et voluptates repudiandae sint et molestiae</p>

  <div class="feature" style="left:82px">
    <div class="badge"><div><svg width="46" height="46" viewBox="0 0 24 24"><path fill="#fff" d="M12 2l2.9 6.6 7.1.6-5.4 4.7 1.6 7L12 17.3 5.8 21l1.6-7L2 9.2l7.1-.6z"/></svg></div></div>
    <h3>EXPERIENCED</h3>
    <p>We provide aggressive legal representation<br>for our clients injured by defective products, motor<br>vehicle accidents, prescription drugs</p>
    <span class="read-more">READ MORE &gt;&gt;</span>
  </div>
  <div class="feature" style="left:440px">
    <div class="badge"><div><svg width="44" height="44" viewBox="0 0 24 24"><rect x="2" y="10" width="4" height="11" fill="#fff"/><path fill="#fff" d="M8 10l4-7c1.5 0 2.3 1 2 2.5L13.4 9H20c1.2 0 2 1 1.8 2.2l-1.4 8c-.2 1-1 1.8-2 1.8H8z"/></svg></div></div>
    <h3>CONFIDENTIAL</h3>
    <p>We provide aggressive legal representation<br>for our clients injured by defective products, motor<br>vehicle accidents, prescription drugs</p>
    <span class="read-more">READ MORE &gt;&gt;</span>
  </div>
  <div class="feature" style="left:796px">
    <div class="badge"><div><svg width="48" height="44" viewBox="0 0 26 22"><rect x="1" y="2" width="24" height="18" rx="1.5" fill="none" stroke="#fff" stroke-width="2"/><rect x="4.5" y="5.5" width="7" height="6" fill="#fff"/><g stroke="#fff" stroke-width="1.6"><line x1="13.5" y1="6.5" x2="21.5" y2="6.5"/><line x1="13.5" y1="10" x2="21.5" y2="10"/><line x1="4.5" y1="14" x2="21.5" y2="14"/><line x1="4.5" y1="17" x2="21.5" y2="17"/></g></svg></div></div>
    <h3>LICENSED</h3>
    <p>We provide aggressive legal representation<br>for our clients injured by defective products, motor<br>vehicle accidents, prescription drugs</p>
    <span class="read-more">READ MORE &gt;&gt;</span>
  </div>
</section>

<section class="practice">
  <h2 class="section-title" style="top:43px">Our Practice Areas</h2>
  <div class="practice-panel">
    <ul class="area-list" style="left:0">
      <li class="active">Crimimal</li>
      <li>Citizenship &amp; Residence</li>
      <li>Sovereign Patron Pathway</li>
      <li style="border-bottom:none">Criminal Defence</li>
    </ul>
    <div class="area-feature" role="img" aria-label="Photo of a person's hands in handcuffs">
      <h4>Crimimal Law</h4>
      <p>Nam libero tempore, cum soluta nobis est eligendi optio cumque nihil impedit quo minus id quod maxime placeat facere</p>
    </div>
    <ul class="area-list right" style="left:732px">
      <li>Civil Litigation</li>
      <li>Arbitration and ADR</li>
      <li>Commercial and Corporate</li>
      <li style="border-bottom:none">Media Law</li>
    </ul>
  </div>
</section>

<section class="testimonials">
  <h2>Client Testimonials</h2>
  <svg class="arrow" style="left:100px" width="12" height="20" viewBox="0 0 12 20"><polyline points="10,2 2,10 10,18" fill="none" stroke="#fff" stroke-width="2.5"/></svg>
  <svg class="arrow" style="left:1088px" width="12" height="20" viewBox="0 0 12 20"><polyline points="2,2 10,10 2,18" fill="none" stroke="#fff" stroke-width="2.5"/></svg>
  <blockquote>“ Atcusamus et iusto odio dignissimos ducimus qui blanditiis praesentium voluptatum deleniti atque corrupti quos dolores et quas molestias excepturi sint occaecati cupiditate non provident, similique sunt in culpa qui officia des erunt mollitia animi, id est laborum et dolorum fuga. ”</blockquote>
  <cite><strong>- LORENZ</strong> <em>(A Landlord &amp; Tenant client)</em></cite>
</section>

<section class="news">
  <h2 class="section-title" style="top:1692px;font-size:28px">LATEST NEWS</h2>
  <article class="news-card" style="left:99px">
    <div class="photo" role="img" aria-label="Photo of classical stone columns against a blue sky" style="background:linear-gradient(180deg,#2b4f9a 0%,#cfd6df 45%,#b8b3a8 100%)"><span class="date">&#9635; 19 DEC 15</span></div>
    <h3>AT VERO EOS ET ACCUSAMUS ET IUSTO ODIO DIGNISSIMOS DUCIM</h3>
    <p>Sed ut perspiciatis unde omnis iste natus errosivolu p atem accusantium doloremque laudantiu tamrem ape riam, eaque ipsa quae ab illo.</p>
    <span class="read-more">READ MORE &gt;&gt;</span>
  </article>
  <article class="news-card" style="left:443px">
    <div class="photo" role="img" aria-label="Photo of hands signing a document at a desk" style="background:linear-gradient(135deg,#2a2a2a 0%,#6c6c6c 45%,#e2e4e6 100%)"><span class="date">&#9635; 19 DEC 15</span></div>
    <h3>AT VERO EOS ET ACCUSAMUS ET IUSTO ODIO DIGNISSIMOS DUCIM</h3>
    <p>Sed ut perspiciatis unde omnis iste natus errosivolu p atem accusantium doloremque laudantiu tamrem ape riam, eaque ipsa quae ab illo.</p>
    <span class="read-more">READ MORE &gt;&gt;</span>
  </article>
  <article class="news-card" style="left:787px">
    <div class="photo" role="img" aria-label="Photo of two businessmen shaking hands between stone columns" style="background:linear-gradient(90deg,#c9c4bb 0%,#9f9a92 50%,#d6d2ca 100%)"><span class="date">&#9635; 19 DEC 15</span></div>
    <h3>AT VERO EOS ET ACCUSAMUS ET IUSTO ODIO DIGNISSIMOS DUCIM</h3>
    <p>Sed ut perspiciatis unde omnis iste natus errosivolu p atem accusantium doloremque laudantiu tamrem ape riam, eaque ipsa quae ab illo.</p>
    <span class="read-more">READ MORE &gt;&gt;</span>
  </article>
  <div class="news-dots"><span class="on"></span><span></span><span></span></div>
</section>

<footer class="site-footer">
  <div class="footer-brand"><span class="name">Mercieca &amp; Ellul</span><span class="sub">ADVOCATES</span></div>

  <h5 style="left:427px">INFORMATION</h5>
  <ul class="footer-links">
    <li>Home</li><li>About us</li><li>Practice Areas</li><li>About Malta</li><li>Contact us</li>
  </ul>

  <h5 style="left:595px">NEWSLETTER SUBSCRIPTION</h5>
  <p class="newsletter-text">Register Your Email Address to get Information about us</p>
  <div class="email-field">Email Address</div>
  <div class="btn-subscribe">SUBSCRIBE</div>

  <h5 style="left:910px">CONTACT US</h5>
  <ul class="contact-list">
    <li><svg width="11" height="14" viewBox="0 0 12 16"><path fill="#e0e0e0" d="M6 0C2.7 0 0 2.6 0 5.9 0 10 6 16 6 16s6-6 6-10.1C12 2.6 9.3 0 6 0zm0 8.2a2.3 2.3 0 110-4.6 2.3 2.3 0 010 4.6z"/></svg><span>12/4, Harbour Lane, Valletta<br>88, Orchard Street, Birkirkara</span></li>
    <li><svg width="13" height="13" viewBox="0 0 16 16"><path fill="#e0e0e0" d="M3.6 1l2.3 3.2-1.4 1.8c.9 2 2.5 3.6 4.5 4.5l1.8-1.4L14 11.4 12.6 15C6.3 14.6 1.4 9.7 1 3.4z"/></svg><span>(356) 2000 1140</span></li>
    <li><svg width="13" height="13" viewBox="0 0 16 16"><path fill="#e0e0e0" d="M3.6 1l2.3 3.2-1.4 1.8c.9 2 2.5 3.6 4.5 4.5l1.8-1.4L14 11.4 12.6 15C6.3 14.6 1.4 9.7 1 3.4z"/></svg><span>(356) 2000 1175</span></li>
    <li><svg width="14" height="11" viewBox="0 0 16 12"><rect width="16" height="12" rx="1" fill="#e0e0e0"/><polyline points="1,1 8,7 15,1" fill="none" stroke="#222428" stroke-width="1.4"/></svg><span style="text-decoration:underline">info@meadvocates.example</span></li>
  </ul>

  <div class="legal">
    <p>© 2016, Mercieca &amp; Ellul. All rights reserved.</p>
    <strong>Terms and a Privacy Statement :</strong>
    <p style="margin-top:4px">Nam libero tempore, cum soluta nobis est eligendi optio cumque nihil impedit quo minus id quod maxime placeat facere possimus, omnis voluptas assumenda est, omnis dolor repellendus.</p>
  </div>
  <div class="social"><span></span><span></span><span></span></div>
</footer>

</body>
</html>
```